Quorva - corporate Business Card

We need a good look and innovative business card for a new start up company based in Los Angeles called "Quorva". We are in a payment business, including payment card, app, and ewallet. We are expert in online payment and Card not present (CNP) transaction.
We need an innovative, modern business card.

Our logo font is Aero Matics

Target Market(s)

Startup - Bank - Online Payment - Card Manufacturing

Industry/Entity Type

Startup

Contact Information for Business Card

phone: 555 014 7396 - Address: 4172 Marlowe blvd, Brinmoor City, NV 89013

Requirements
Must have
• Message: innovative, professional, expert, high tech, trust, online payment expert, security
Nice to have
• no comment
Should not have
• no Comment

```html
<!DOCTYPE html>
<html lang="en">
<head>
<meta charset="utf-8">
<title>Quorva — Business Card</title>
<link rel="stylesheet" href="https://fonts.googleapis.com/css2?family=Open+Sans:wght@400;600;700&display=swap">
<style>
  :root {
    --brand-red: #c8102e;
    --brand-red-deep: #a90a20;
    --brand-red-light: #d7223a;
    --card-white: #ffffff;
    --text-grey: #8a8a8a;
    --stage: #bdbdbd;
    --card-shadow: rgba(0, 0, 0, 0.22);
  }
  * { margin: 0; padding: 0; box-sizing: border-box; }
  html, body {
    width: 1200px;
    height: 837px;
    overflow: hidden;
    background: var(--stage);
    font-family: "Open Sans", Arial, sans-serif;
  }
  .canvas {
    position: relative;
    width: 1200px;
    height: 837px;
    display: flex;
    align-items: center;
    justify-content: center;
    gap: 60px;
  }
  .card {
    position: relative;
    width: 520px;
    height: 297px;
    box-shadow: 0 10px 24px var(--card-shadow);
    overflow: hidden;
  }

  /* Front side */
  .card--front {
    background: var(--brand-red);
  }
  .card__texture {
    position: absolute;
    inset: 0;
    background: linear-gradient(135deg, var(--brand-red-deep) 0%, var(--brand-red) 50%, var(--brand-red-light) 100%);
  }
  .card__wordmark {
    position: absolute;
    inset: 0;
    display: flex;
    align-items: center;
    justify-content: center;
    color: var(--card-white);
    font-weight: 700;
    font-size: 72px;
    letter-spacing: 1px;
  }

  /* Back side */
  .card--back {
    background: var(--card-white);
  }
  .brand {
    position: absolute;
    top: 34px;
    left: 36px;
    display: flex;
    align-items: center;
    gap: 10px;
  }
  .brand__dot {
    width: 50px;
    height: 50px;
    border-radius: 50%;
    background: var(--brand-red);
  }
  .brand__name {
    color: var(--brand-red);
    font-weight: 700;
    font-size: 42px;
    line-height: 1;
  }
  .contact {
    position: absolute;
    right: 34px;
    bottom: 30px;
    text-align: right;
    font-size: 13px;
    line-height: 1.35;
    color: var(--text-grey);
  }
  .contact__name {
    color: var(--brand-red);
    font-weight: 700;
    font-size: 17px;
    line-height: 1.1;
  }
  .contact__role {
    margin-bottom: 10px;
  }
  .contact__label {
    color: var(--brand-red);
    font-weight: 700;
  }
</style>
</head>
<body>
<main class="canvas">
  <section class="card card--front">
    <div class="card__texture" role="img" aria-label="Subtle interlocking geometric pattern in tones of red"></div>
    <div class="card__wordmark">quorva</div>
  </section>

  <section class="card card--back">
    <div class="brand">
      <span class="brand__dot"></span>
      <span class="brand__name">quorva</span>
    </div>
    <div class="contact">
      <p class="contact__name">Dana Whitlow</p>
      <p class="contact__role">Managing Director</p>
      <p><span class="contact__label">P:</span> 555 014 7396</p>
      <p>4172 Marlowe blvd</p>
      <p>Brinmoor City, NV 89013</p>
    </div>
  </section>
</main>
</body>
</html>
```